July 2022 Industrial Manufacturer Product Expo Mexico City

We manufacture large screws and fastners for large Mining equipment, Trains, large ships, airplanes, wind turbines, and so on. We also do custom work base on the customer needs. No matter the size we can make it.
We have a Expo coming up with companies all over the world. We have to stand out we are a family own business so our customer service will be above and beyond anyone can provide. We do not have a sales force to push our products and services we provide one on one service.
Plus@!! I'm looking for anything that you designers can come up with if it was your company to put on a business card, plus i want to do a 1 or 2 sided pamphlet, and then a website. We make Speciality Bolts for large mining equipment these bolts can be 3 to 4 foot long!!! Plus fasteners, Nuts, washers, any, size, strengths, special materials, we offer more of a ono on one customer service, We are a small company, family own, but can fulfill any type of orders. We can also provide special time lines for emergency orders. "We keep the machines running we here at KRV don't believe in down time" We want to hear any slogan based on our company to stand out.
Thanks i really appreciate all your work and options that we have to pick on. Plus just a thought we could possibly want to entertain a experience Marketing internet help maybe a employment possibility. Thanks

I need 2 cards one in Spanish and English Like the steel back ground maybe send me in some bright red and blue writing Same with the Black cards Please remove the word Military The logo KRV maybe integrate a picture of a Bolt 🔩 Thank you

Still looking for I need 2 cards one in Spanish and English Like the steel back ground maybe send me in some bright red and blue writing Same with the Black cards try bright writing Please remove the word Military The logo KRV maybe integrate a picture of a Bolt 🔩 Plus will need the company to make a brochure and website next Thank you

Target Market(s)

Large Mining, Ship, Train, Green Energy, VELM, and Government equipment. Throughout the World

Industry/Entity Type

We can Custom Manufacture any type of Fastners for Mining equipment, Trains, Ships, Green energy, Governments, or military projects. wind turbines,

Contact Information for Business Card

I attached the name and contact info that's on a card, plus the Company Logo. Would like industrial looking background with Bright Colors that will stand out!! If we can insert somewhere maybe on back that we "Custom Manufacture Any Size or Quantity Fastners for Large Mining Equipment, Trains, Ships, Green Energy Equipment or Government Projects

Font styles to use
Other font styles liked:
• You Pick, has to be bold, colorful standout, Professional looking Beable to read it.

Colors

Designer to choose colors to be used in the design.

Requirements
Must have
• Need in Spanish and English TO STANDOUT FROM THE REST OF THE EXPO!! See Business card details, Rounded corners
Nice to have
• Can i see some of the darker cards with Bright Red and Blue letters I like to see the different type of card material, heavy thickness, plastic, transparent, Metal types, Bright Colors, I saw like Raised letters like on the logo.

```html
<!DOCTYPE html>
<html lang="en">
<head>
<meta charset="utf-8">
<title>KRV Business Cards</title>
<link href="https://fonts.googleapis.com/css2?family=Tinos:wght@400;700&display=swap" rel="stylesheet">
<style>
  :root{
    --stage:#1d1d1f;
    --card-top:#7a7a7c;
    --card-mid:#2a2a2c;
    --card-bottom:#0f0f10;
    --band-dark:#0a2a8a;
    --band-light:#0a8fd6;
    --accent:#1a8fe0;
    --accent-red:#ff2d2d;
    --text-light:#f4f4f4;
    --white:#ffffff;
    --logo-steel:#b9bcc0;
    --logo-ink:#3a3b3e;
  }
  *{margin:0;padding:0;box-sizing:border-box}
  html,body{width:1200px;height:1015px;overflow:hidden}
  body{
    background:var(--stage);
    font-family:"Tinos","Times New Roman",serif;
    display:flex;flex-direction:column;align-items:center;justify-content:center;gap:48px;
  }
  .card{
    width:760px;height:434px;border-radius:14px;overflow:hidden;position:relative;
    box-shadow:0 18px 40px rgba(0,0,0,.6);
  }
  /* front */
  .card-front{
    background:linear-gradient(180deg,var(--card-top) 0%,var(--card-mid) 45%,var(--card-bottom) 100%);
  }
  .card-front .brand{
    position:absolute;left:0;right:0;top:0;height:238px;
    display:flex;align-items:center;justify-content:center;gap:18px;
  }
  .brand-name{font-weight:700;letter-spacing:.06em;line-height:1}
  .card-front .brand-name{font-size:116px;color:var(--logo-steel)}
  .brand-mark{width:22px;height:22px;border-radius:50%;background:var(--accent-red)}
  .tagline-band{
    position:absolute;left:0;right:0;bottom:0;height:196px;
    background:linear-gradient(180deg,var(--band-dark) 0%,var(--band-light) 100%);
    display:flex;flex-direction:column;align-items:center;justify-content:center;gap:12px;
    text-align:center;padding:0 56px;
  }
  .tagline{color:var(--text-light);font-size:20px;line-height:1.25}
  .tagline-es{color:var(--text-light);font-size:17px;line-height:1.25;font-style:normal;opacity:.92}
  /* back */
  .card-back{
    display:flex;
    background:linear-gradient(180deg,var(--card-top) 0%,var(--card-mid) 40%,var(--card-bottom) 100%);
  }
  .logo-panel{
    width:42%;background:var(--white);border-right:4px solid var(--band-dark);
    display:flex;align-items:center;justify-content:center;gap:12px;
  }
  .logo-panel .brand-name{font-size:84px;color:var(--logo-ink)}
  .contact-panel{flex:1;padding:90px 36px 0 48px;color:var(--text-light)}
  .contact-name{color:var(--accent);font-size:34px;font-weight:400;margin-bottom:22px;white-space:nowrap}
  .contact-role{font-size:21px;line-height:1.3;color:var(--accent-red);font-weight:700}
  .contact-email{font-size:21px;line-height:1.3}
  .phone-list{list-style:none;margin-top:22px}
  .phone-list li{display:flex;align-items:center;gap:12px;font-size:24px;line-height:1.35}
  .phone-list svg{width:20px;height:20px;flex:none}
</style>
</head>
<body>

<section class="card card-front" aria-label="Business card front">
  <div class="brand">
    <span class="brand-name">KRV</span>
    <span class="brand-mark"></span>
  </div>
  <div class="tagline-band">
    <p class="tagline" lang="en">Custom Manufacture Any Size or Quantity Fastners for Large Mining Equipment,<br>Trains, Ships, Green Energy Equipment or Government Projects</p>
    <p class="tagline-es" lang="es">Fabricamos a la medida sujetadores de cualquier tamaño o cantidad para equipo<br>minero, trenes, barcos, equipo de energía verde o proyectos de gobierno</p>
  </div>
</section>

<section class="card card-back" aria-label="Business card back">
  <div class="logo-panel">
    <span class="brand-name">KRV</span>
    <span class="brand-mark"></span>
  </div>
  <div class="contact-panel">
    <h1 class="contact-name">Lic. Daniela Ortiz Varela</h1>
    <p class="contact-role">Cotizaciones en / Quotes at</p>
    <p class="contact-email">krv.ventas@correo.mx</p>
    <ul class="phone-list">
      <li>
        <svg viewBox="0 0 24 24" aria-hidden="true"><path d="M6.6 10.8a15.1 15.1 0 0 0 6.6 6.6l2.2-2.2a1 1 0 0 1 1-.25 11.4 11.4 0 0 0 3.6.57 1 1 0 0 1 1 1V20a1 1 0 0 1-1 1A17 17 0 0 1 3 4a1 1 0 0 1 1-1h3.5a1 1 0 0 1 1 1c0 1.25.2 2.45.57 3.57a1 1 0 0 1-.25 1z" fill="#1a8fe0"/></svg>
        5550192837
      </li>
      <li>
        <svg viewBox="0 0 24 24" aria-hidden="true"><rect x="6" y="2" width="12" height="20" rx="2" fill="none" stroke="#1a8fe0" stroke-width="2"/><circle cx="12" cy="18" r="1.2" fill="#1a8fe0"/></svg>
        5550146620
      </li>
    </ul>
  </div>
</section>

</body>
</html>
```